Plakate für Haushaltshilfen und Alltagsbegleiter
Zielgruppe
Wir bieten haushaltsnahe Dienstleistungen (Haushaltshilfen und Altgasbegleiter) für Personen mit einem Pflegegrad 1 - 5 an.
Zielgruppe sind Personen mit einem Pflegegrad 1 - 5. Hauptsächlich ältere Menschen die Unterstützung/Betreuung im Alltag und Haushalt benötigen.
Aufgabenstellung
Wir benötigen für unsere Büroräume eine Fensterbeschriftung. Es handelt sich hier um 5 Fenster (Glasflächen) und eine Glastür. Die Vorgabe ist, dass von außen zu erkennen ist dass sich um alle Räumlichkeiten um unsere (Firma Lindwerk) Räumlichkeiten handelt. Desweiteren soll auch unser Angebot erkennbar sein.
Unser Angebot enthält: Haushaltshilfen und Alltagsbegleiter
- kostenlose Haushaltshilfe ab Pflegegrad 1
- Abrechnung mit allen Kostenträgern
Da wir keine Schilder an die Fassade anbringen können, müßen die Glasflächen dafür genutzt werden um zum Einen uns als Firma erkennbar zu machen und zum anderen unser Angebot kurz zu präsentieren.
Uns ist wichtig dass unser Logo verwendet wir und auch unsere Farben.
Desweiteren sollten an den Fenstern auch teilweise eine Sichtschutz nach innen, angebracht werden, aber eben nur teilweise also nicht das ganzen Fenster z.Bsp. mit einer Blickdichten Folie überziehen, sondern in Augenhöhe wenn Fußgänger vorbei laufen.

```html
<!DOCTYPE html>
<html lang="de">
<head>
<meta charset="utf-8">
<title>Lindwerk – Plakate und Fensterfolien</title>
<link href="https://fonts.googleapis.com/css2?family=Cinzel:wght@600&family=Raleway:wght@300;600;700&family=Gochi+Hand&display=swap" rel="stylesheet">
<style>
  :root{
    --brand-red:#c4161c;
    --brand-red-light:#d63a3f;
    --paper:#f2f2f2;
    --footer-dark:#333333;
    --stage:#b9babc;
    --foil-grey:#d9d9da;
    --foil-dark:#3a3a3c;
    --ink:#2b2b2b;
  }
  *{box-sizing:border-box;margin:0;padding:0}
  html,body{width:723px;height:1200px;overflow:hidden}
  body{background:var(--stage);font-family:"Raleway",sans-serif;color:var(--ink)}

  .poster-row{display:flex;justify-content:space-between;padding:74px 34px 0 33px;height:440px}
  .poster{width:206px;height:289px;background:var(--paper);display:flex;flex-direction:column;box-shadow:0 2px 4px rgba(0,0,0,.2)}
  .poster-title{height:54px;display:flex;align-items:center;justify-content:center;font-family:"Cinzel",serif;font-weight:600;color:var(--brand-red);font-size:17.5px;letter-spacing:.3px}
  .poster-title.is-long{font-size:15px}
  .offer-band{position:relative;height:127px;background:var(--brand-red);color:#fff;padding:13px 0 0 16px}
  .offer-band.is-compact{padding-top:32px}
  .offer-heading{font-weight:600;font-size:9.2px;line-height:1.18}
  .offer-list{list-style:none;margin-top:6px;font-weight:300;font-size:7.2px;line-height:1.18}
  .offer-list li{position:relative;padding-left:5px;margin-bottom:5px}
  .offer-list li::before{content:"•";position:absolute;left:-1px;font-size:5px;top:1px}
  .benefit-pill{position:absolute;left:0;top:91px;width:113px;height:22px;background:var(--paper);border-radius:0 11px 11px 0;color:var(--ink);font-weight:700;font-size:3.6px;line-height:1.3;padding:3px 0 0 16px}
  .service-icon{position:absolute;right:16px;top:26px;width:66px;height:68px;background:var(--brand-red-light);border-radius:8px}
  .offer-band.is-compact .service-icon{top:26px}
  .poster-claim{flex:1;display:flex;flex-direction:column;align-items:center;padding-top:12px}
  .claim-line{font-family:"Gochi Hand",cursive;color:var(--brand-red);font-size:12px;letter-spacing:.6px}
  .brand-mark{display:flex;flex-direction:column;align-items:center;margin-top:5px}
  .brand-ring{width:28px;height:28px;border:3px solid var(--brand-red);border-radius:50%}
  .brand-name{font-family:"Cinzel",serif;font-weight:600;color:var(--brand-red);font-size:10px;margin-top:4px;letter-spacing:.4px}
  .contact-bar{height:21px;background:var(--footer-dark);color:#fff;display:flex;align-items:center;justify-content:space-between;padding:0 10px 0 16px;font-size:4.6px;font-weight:300}
  .contact-item{display:flex;align-items:center;gap:3px}
  .contact-item svg{width:6px;height:6px}
  .chat-dot{width:6px;height:6px;border:.7px solid #fff;border-radius:50%}

  .foil-row{display:flex;justify-content:space-around;align-items:center;height:720px;padding:0 20px}
  .window-foil{width:210px;height:350px;background:var(--foil-grey);display:flex;flex-direction:column}
  .foil-screen{height:62px;background:linear-gradient(180deg,#2e2e30 0%,#8a8a8c 55%,var(--foil-grey) 100%)}
  .foil-body{flex:1;display:flex;flex-direction:column;align-items:center;padding-top:24px;text-align:center}
  .foil-body .brand-ring{width:46px;height:46px;border-width:4px}
  .foil-body .brand-name{font-size:16px;margin-top:6px}
  .foil-heading{font-weight:700;font-size:7.4px;margin-top:12px;color:#444}
  .foil-note{font-weight:300;font-size:6px;margin-top:5px;color:#555}
  .foil-cta{height:66px;background:var(--foil-dark);color:#fff;text-align:center;padding-top:10px}
  .foil-cta-title{font-weight:700;font-size:8.6px}
  .foil-cta .contact-bar{background:none;height:16px;padding:0 12px;font-size:4px}
  .foil-web{font-weight:700;font-size:5.5px}
  .door-foil{width:170px;height:520px;background:var(--foil-grey);display:flex;flex-direction:column}
  .door-top{height:100px;background:linear-gradient(180deg,#2e2e30 0%,#8a8a8c 60%,var(--foil-grey) 100%)}
  .door-mid{flex:1;display:flex;align-items:center;justify-content:center}
  .door-mid .brand-ring{width:60px;height:60px;border-width:5px}
  .door-mid .brand-name{font-size:19px;margin-top:8px}
  .door-bottom{height:190px;background:linear-gradient(180deg,var(--foil-grey) 0%,#7d7d80 40%,#2e2e30 100%)}
</style>
</head>
<body>

<section class="poster-row">
  <article class="poster">
    <h2 class="poster-title">HAUSHALTSHILFE</h2>
    <div class="offer-band">
      <p class="offer-heading">Haushaltshilfen<br>und Alltagsbegleiter</p>
      <ul class="offer-list"><li>kostenlose Haushaltshilfe<br>ab Pflegegrad 1</li><li>Abrechnung mit<br>allen Kostenträgern</li></ul>
      <div class="benefit-pill">Nutzen Sie Ihren Entlastungsbetrag<br>ab Pflegegrad 1 und Ihre Verhinderungspflege<br>ab dem Pflegegrad 2</div>
      <div class="service-icon" role="img" aria-label="Linien-Symbol eines Staubsaugers"></div>
    </div>
    <div class="poster-claim">
      <p class="claim-line">Wir sind für Sie da!</p>
      <div class="brand-mark"><span class="brand-ring"></span><span class="brand-name">LINDWERK</span></div>
    </div>
    <footer class="contact-bar">
      <span class="contact-item"><svg viewBox="0 0 10 10"><path d="M2 1l2 2-1 1.2c.6 1.2 1.5 2.1 2.8 2.8L7 6l2 2-1.3 1.3C4.5 9 1 5.5.7 2.3z" fill="#fff"/></svg>0711 38 22 90 57</span>
      <span class="contact-item"><span class="chat-dot"></span>0176 21 84 39 15</span>
      <span class="contact-item"><svg viewBox="0 0 10 10"><rect x=".5" y="2" width="9" height="6" fill="none" stroke="#fff" stroke-width=".8"/><path d="M.5 2l4.5 3.5L9.5 2" fill="none" stroke="#fff" stroke-width=".8"/></svg>info@lindwerk.de</span>
    </footer>
  </article>

  <article class="poster">
    <h2 class="poster-title">EINKAUFSSERVICE</h2>
    <div class="offer-band is-compact">
      <p class="offer-heading">Haushaltshilfen<br>und Alltagsbegleiter</p>
      <ul class="offer-list"><li>kostenlose Haushaltshilfe<br>ab Pflegegrad 1</li><li>Abrechnung mit<br>allen Kostenträgern</li></ul>
      <div class="service-icon" role="img" aria-label="Linien-Symbol einer Einkaufstüte"></div>
    </div>
    <div class="poster-claim">
      <p class="claim-line">Wir sind für Sie da!</p>
      <div class="brand-mark"><span class="brand-ring"></span><span class="brand-name">LINDWERK</span></div>
    </div>
    <footer class="contact-bar">
      <span class="contact-item"><svg viewBox="0 0 10 10"><path d="M2 1l2 2-1 1.2c.6 1.2 1.5 2.1 2.8 2.8L7 6l2 2-1.3 1.3C4.5 9 1 5.5.7 2.3z" fill="#fff"/></svg>0711 38 22 90 57</span>
      <span class="contact-item"><span class="chat-dot"></span>0176 21 84 39 15</span>
      <span class="contact-item"><svg viewBox="0 0 10 10"><rect x=".5" y="2" width="9" height="6" fill="none" stroke="#fff" stroke-width=".8"/><path d="M.5 2l4.5 3.5L9.5 2" fill="none" stroke="#fff" stroke-width=".8"/></svg>info@lindwerk.de</span>
    </footer>
  </article>

  <article class="poster">
    <h2 class="poster-title is-long">ALLTAGSBEGLEITUNG</h2>
    <div class="offer-band">
      <p class="offer-heading">Haushaltshilfen<br>und Alltagsbegleiter</p>
      <ul class="offer-list"><li>kostenlose Haushaltshilfe<br>ab Pflegegrad 1</li><li>Abrechnung mit<br>allen Kostenträgern</li></ul>
      <div class="benefit-pill">Nutzen Sie Ihren Entlastungsbetrag<br>ab Pflegegrad 1 und Ihre Verhinderungspflege<br>ab dem Pflegegrad 2</div>
      <div class="service-icon" role="img" aria-label="Linien-Symbol eines Herzens mit Gehstock"></div>
    </div>
    <div class="poster-claim">
      <p class="claim-line">Wir sind für Sie da!</p>
      <div class="brand-mark"><span class="brand-ring"></span><span class="brand-name">LINDWERK</span></div>
    </div>
    <footer class="contact-bar">
      <span class="contact-item"><svg viewBox="0 0 10 10"><path d="M2 1l2 2-1 1.2c.6 1.2 1.5 2.1 2.8 2.8L7 6l2 2-1.3 1.3C4.5 9 1 5.5.7 2.3z" fill="#fff"/></svg>0711 38 22 90 57</span>
      <span class="contact-item"><span class="chat-dot"></span>0176 21 84 39 15</span>
      <span class="contact-item"><svg viewBox="0 0 10 10"><rect x=".5" y="2" width="9" height="6" fill="none" stroke="#fff" stroke-width=".8"/><path d="M.5 2l4.5 3.5L9.5 2" fill="none" stroke="#fff" stroke-width=".8"/></svg>info@lindwerk.de</span>
    </footer>
  </article>
</section>

<section class="foil-row">
  <article class="window-foil">
    <div class="foil-screen"></div>
    <div class="foil-body">
      <div class="brand-mark"><span class="brand-ring"></span><span class="brand-name">LINDWERK</span></div>
      <p class="foil-heading">Haushaltshilfen und Alltagsbegleiter</p>
      <p class="foil-note">kostenlose Haushaltshilfe ab Pflegegrad 1</p>
      <p class="foil-note">Abrechnung mit allen Kostenträgern</p>
    </div>
    <footer class="foil-cta">
      <p class="foil-cta-title">Jetzt Termin vereinbaren!</p>
      <div class="contact-bar">
        <span class="contact-item">0711 38 22 90 57</span>
        <span class="contact-item"><span class="chat-dot"></span>0176 21 84 39 15</span>
        <span class="contact-item">info@lindwerk.de</span>
      </div>
      <p class="foil-web">www.lindwerk.de</p>
    </footer>
  </article>

  <article class="door-foil">
    <div class="door-top"></div>
    <div class="door-mid">
      <div class="brand-mark"><span class="brand-ring"></span><span class="brand-name">LINDWERK</span></div>
    </div>
    <div class="door-bottom"></div>
  </article>

  <article class="window-foil">
    <div class="foil-screen"></div>
    <div class="foil-body">
      <div class="brand-mark"><span class="brand-ring"></span><span class="brand-name">LINDWERK</span></div>
      <p class="foil-heading">Haushaltshilfen und Alltagsbegleiter</p>
      <p class="foil-note">kostenlose Haushaltshilfe ab Pflegegrad 1</p>
      <p class="foil-note">Abrechnung mit allen Kostenträgern</p>
    </div>
    <footer class="foil-cta">
      <p class="foil-cta-title">Jetzt Termin vereinbaren!</p>
      <div class="contact-bar">
        <span class="contact-item">0711 38 22 90 57</span>
        <span class="contact-item"><span class="chat-dot"></span>0176 21 84 39 15</span>
        <span class="contact-item">info@lindwerk.de</span>
      </div>
      <p class="foil-web">www.lindwerk.de</p>
    </footer>
  </article>
</section>

</body>
</html>
```